Pharmacy ad

need 2 pharmacy ads for the phone book. one for Brookvale Pharmacy and one for Cedarline Care Pharmacy. Dimensions for ad is 4.75in x 4.667 in. please see attached examples of ad uploaded as well logos of each pharmacy

```html
<!DOCTYPE html>
<html lang="en">
<head>
<meta charset="utf-8">
<title>Pharmacy Directory Ads</title>
<link rel="stylesheet" href="https://fonts.googleapis.com/css2?family=Barlow:ital,wght@0,400;0,500;0,600;0,700;1,500&family=Barlow+Condensed:wght@700&family=Barlow+Semi+Condensed:wght@400;700&family=Oswald:wght@500;600&family=Passion+One&display=swap">
<style>
:root{
  --board:#fdf1a0;
  --navy:#1b1f4a;
  --ink:#151a3a;
  --royal:#3550a3;
  --green:#86c440;
  --green-deep:#5fae2e;
  --white:#ffffff;
  --chip-line:#c9cfdc;
}
*{box-sizing:border-box;margin:0;padding:0}
html,body{width:1200px;height:600px;overflow:hidden}
body{background:var(--board);font-family:"Barlow",sans-serif;position:relative}
.ad{position:absolute;top:22px;width:564px;height:554px;overflow:hidden}
.ad svg.backdrop{position:absolute;inset:0}
.ad--brookvale{left:22px;border:2px solid var(--navy);color:var(--navy)}
.ad--cedarline{left:614px;width:565px;border:2px solid var(--green);color:var(--royal);background:var(--white)}

/* shared */
.chips{position:absolute;display:flex;flex-wrap:wrap;gap:6px;justify-content:center}
.chip{background:var(--white);border:1px solid var(--chip-line);font-weight:600;font-size:10px;color:var(--navy);height:28px;padding:0 7px;display:flex;align-items:center}
.services{position:absolute;display:flex;font-size:12.5px;line-height:1.1}
.services ul{list-style:none;display:flex;flex-direction:column}
.services li{padding-left:11px;position:relative}
.services li::before{content:"";position:absolute;left:0;top:4px;width:5px;height:5px;background:currentColor;transform:rotate(45deg)}
.hours{position:absolute;font-weight:700}
.hours small{font-weight:400;font-size:11px}
.pin,.phone{width:11px;height:13px}
.social{position:absolute;text-align:center;font-size:13px}
.social .dot{border-radius:50%;background:var(--royal);margin:4px auto 0;display:flex;align-items:center;justify-content:center;color:var(--white);font-weight:600;font-size:10px}

/* Brookvale */
.promo{position:absolute;left:8px;top:24px;width:254px;text-align:center;line-height:1}
.promo .pct{font-weight:700;font-size:42px;letter-spacing:-1px}
.promo .label{font-size:19.5px;font-weight:400}
.promo .cond{font-size:18.5px;font-weight:700;margin-top:2px}
.promo .dots{letter-spacing:4px;font-weight:700;font-size:14px;margin:10px 0 4px}
.brand{position:absolute;left:292px;top:28px;width:270px;text-align:center}
.brand .mark{width:84px;height:84px;border-radius:50%;background:var(--green);margin:0 auto 46px}
.brand .name{font-weight:700;font-size:40px;line-height:1;color:var(--navy);letter-spacing:.5px}
.brand .tagline{font-style:italic;font-weight:500;font-size:14.5px;color:var(--green-deep);margin-top:8px}
.ad--brookvale .chips{left:364px;top:318px;width:190px}
.ad--brookvale .services{left:30px;top:286px}
.ad--brookvale .services ul{gap:7px}
.ad--brookvale .services ul:first-child{width:142px}
.ad--brookvale .services ul:last-child{gap:9px}
.rule{position:absolute;left:26px;top:403px;width:330px;height:2px;background:var(--navy)}
.ad--brookvale .hours{left:26px;top:412px;font-size:16.5px;line-height:22.5px}
.addr{position:absolute;font-size:12px;font-weight:600;line-height:1.25;display:grid;grid-template-columns:18px auto;row-gap:1px}
.addr .note{font-weight:400;font-size:10.5px}
.addr svg{margin-top:1px}
.ad--brookvale .addr.main{left:30px;top:492px}
.ad--brookvale .addr.port{left:294px;top:492px}
.ad--brookvale .social{left:465px;top:478px;width:80px}
.ad--brookvale .social .dot{width:46px;height:46px}

/* Cedarline */
.photo{position:absolute;left:0;top:0;width:565px;height:205px;background:linear-gradient(90deg,#eef3f6 0%,#e6ecef 55%,#cfd8dc 75%,#b9a79a 100%)}
.c-mark{position:absolute;left:30px;top:22px;width:80px;height:80px;border-radius:50%;background:var(--royal)}
.c-name{position:absolute;left:132px;top:40px;text-align:center;font-weight:600;color:var(--royal);line-height:1}
.c-name .main{font-size:40px}
.c-name .sub{display:block;font-size:21px;letter-spacing:1px;margin-top:4px}
.accept{position:absolute;left:78px;top:128px;font-weight:700;font-size:12px;color:var(--ink)}
.ad--cedarline .chips{left:78px;top:144px;gap:5px;flex-wrap:nowrap}
.ad--cedarline .chip{height:26px;font-size:9.5px;color:var(--ink)}
.motto{position:absolute;left:0;width:565px;top:216px;text-align:center;font-family:"Passion One",sans-serif;font-size:48px;color:var(--royal);letter-spacing:.5px}
.offers{position:absolute;left:30px;top:314px;display:grid;grid-template-columns:auto auto;column-gap:6px;row-gap:8px;align-items:center}
.offers .pct{font-family:"Barlow Condensed",sans-serif;font-weight:700;font-size:68px;line-height:.85;letter-spacing:-1px}
.offers .label{font-family:"Barlow Semi Condensed",sans-serif;font-weight:400;font-size:19px;line-height:.95}
.offers .label b{display:block;font-weight:400;font-size:28px}
.offers .label small{display:block;font-weight:700;font-size:10.5px}
.divider{position:absolute;left:278px;top:296px;width:3px;height:140px;background:var(--green)}
.ad--cedarline .services{left:292px;top:318px;font-size:12px}
.ad--cedarline .services ul:first-child{width:138px;gap:7px}
.ad--cedarline .services ul:last-child{gap:10px}
.ad--cedarline .services li::before{border-radius:50%;transform:none;width:4px;height:4px;top:5px}
.footer{position:absolute;left:0;top:446px;width:565px;height:108px;background:var(--green)}
.ad--cedarline .hours{left:28px;top:460px;font-family:"Oswald",sans-serif;font-weight:600;font-size:19px;line-height:25px;color:var(--ink);letter-spacing:.5px}
.c-contact{position:absolute;left:28px;top:518px;display:flex;gap:26px;font-family:"Oswald",sans-serif;font-weight:500;font-size:13px;color:var(--ink);align-items:center}
.c-contact span{display:flex;align-items:center;gap:4px}
.ad--cedarline .social{left:462px;top:468px;width:80px;color:var(--royal)}
.ad--cedarline .social .dot{width:52px;height:52px}
</style>
</head>
<body>

<section class="ad ad--brookvale" aria-label="Brookvale Pharmacy ad">
  <svg class="backdrop" width="564" height="554" viewBox="0 0 564 554" aria-hidden="true">
    <defs>
      <linearGradient id="skyWash" x1="0" y1="0" x2="1" y2="1">
        <stop offset="0" stop-color="#8fcbea"/><stop offset="1" stop-color="#cde8f5"/>
      </linearGradient>
      <linearGradient id="meadowWash" x1="0" y1="0" x2="0" y2="1">
        <stop offset="0" stop-color="#a5d272"/><stop offset="1" stop-color="#d5ebb8"/>
      </linearGradient>
    </defs>
    <rect width="564" height="554" fill="url(#skyWash)"/>
    <rect y="268" width="564" height="286" fill="url(#meadowWash)"/>
    <ellipse cx="480" cy="130" rx="250" ry="320" fill="#7cc2e6"/>
    <ellipse cx="480" cy="100" rx="232" ry="232" fill="#f7fbfd"/>
  </svg>

  <div class="promo">
    <div class="pct">10%</div>
    <div class="label">SENIOR CITIZEN<br>DISCOUNT</div>
    <div class="cond">FOR PATIENTS 60<br>YEARS AND OVER</div>
    <div class="dots">• • • • • • • • • • • • • •</div>
    <div class="pct">10%</div>
    <div class="label">STUDENT DISCOUNT</div>
    <div class="cond">WITH VALID ID CARD</div>
  </div>

  <div class="brand">
    <div class="mark"></div>
    <div class="name">BROOKVALE<br>PHARMACY</div>
    <div class="tagline">We Care About Your Health</div>
  </div>

  <div class="chips">
    <span class="chip">Paycard</span>
    <span class="chip">Cardmark</span>
    <span class="chip">Harbor Life</span>
    <span class="chip">Islecover</span>
  </div>

  <div class="services">
    <ul>
      <li>Certified Pharmacists</li>
      <li>Affordable prices</li>
      <li>Brand and<br>Generic Medicines</li>
      <li>Blood Pressure and<br>Glucose checks</li>
    </ul>
    <ul>
      <li>Personal care and<br>Beauty Products</li>
      <li>Injectables</li>
      <li>Special Orders</li>
      <li>Delivery service</li>
    </ul>
  </div>

  <div class="rule"></div>

  <div class="hours">
    MONDAY – FRIDAY 10AM TO 6PM<br>
    SATURDAY 10AM TO 5PM<br>
    SUNDAY 10AM TO 2PM <small>(MARLOW STREET BRANCH)</small>
  </div>

  <div class="addr main">
    <svg class="pin" viewBox="0 0 12 16" aria-hidden="true"><path d="M6 0a6 6 0 0 0-6 6c0 4.5 6 10 6 10s6-5.5 6-10a6 6 0 0 0-6-6zm0 8.5A2.5 2.5 0 1 1 6 3.5a2.5 2.5 0 0 1 0 5z" fill="currentColor"/></svg>
    <span>19 Marlow Street, Easthaven<br><span class="note">(opposite Grace Hill Chapel)</span></span>
    <svg class="phone" viewBox="0 0 16 14" aria-hidden="true"><path d="M2 5c0-3 2-4 6-4s6 1 6 4h-3V3.5H5V5zM3 6h10l1 7H2z" fill="currentColor"/></svg>
    <span>555-0174</span>
  </div>

  <div class="addr port">
    <svg class="pin" viewBox="0 0 12 16" aria-hidden="true"><path d="M6 0a6 6 0 0 0-6 6c0 4.5 6 10 6 10s6-5.5 6-10a6 6 0 0 0-6-6zm0 8.5A2.5 2.5 0 1 1 6 3.5a2.5 2.5 0 0 1 0 5z" fill="currentColor"/></svg>
    <span>Quayside Court, Food Court,<br>Easthaven</span>
    <svg class="phone" viewBox="0 0 16 14" aria-hidden="true"><path d="M2 5c0-3 2-4 6-4s6 1 6 4h-3V3.5H5V5zM3 6h10l1 7H2z" fill="currentColor"/></svg>
    <span>555-0177</span>
  </div>

  <div class="social">Visit us on<div class="dot">Linkly</div></div>
</section>

<section class="ad ad--cedarline" aria-label="Cedarline Care Pharmacy ad">
  <div class="photo" role="img" aria-label="Photo of a smiling pharmacist in glasses reaching for a medicine shelf"></div>
  <svg class="backdrop" width="565" height="554" viewBox="0 0 565 554" aria-hidden="true">
    <path d="M0 178 C150 215 330 225 565 165 L565 300 C420 300 200 275 0 300 Z" fill="#a9d6ef"/>
    <path d="M0 178 C150 215 330 225 565 165" fill="none" stroke="#86c440" stroke-width="6"/>
    <path d="M0 184 C150 221 330 231 565 171" fill="none" stroke="#3550a3" stroke-width="3"/>
    <path d="M0 300 C200 275 420 290 565 300 L565 554 L0 554 Z" fill="#ffffff"/>
    <path d="M0 296 C200 270 420 285 565 300" fill="none" stroke="#1b2a7a" stroke-width="4"/>
    <path d="M0 302 C200 276 420 291 565 306" fill="none" stroke="#86c440" stroke-width="4"/>
  </svg>

  <div class="c-mark"></div>
  <div class="c-name"><span class="main">Cedarline Care</span><span class="sub">PHARMACY</span></div>

  <div class="accept">WE ACCEPT:</div>
  <div class="chips">
    <span class="chip">Paycard</span>
    <span class="chip">Cardmark</span>
    <span class="chip">Harbor Life</span>
    <span class="chip">Islecover</span>
  </div>

  <div class="motto">Where good health begins</div>

  <div class="offers">
    <div class="pct">10%</div>
    <div class="label">SENIOR CITIZEN<b>DISCOUNT</b></div>
    <div class="pct">10%</div>
    <div class="label">STUDENT<b>DISCOUNT</b><small>(WITH VALID ID CARD)</small></div>
  </div>

  <div class="divider"></div>

  <div class="services">
    <ul>
      <li>Certified Pharmacists</li>
      <li>Affordable prices</li>
      <li>Brand and<br>Generic Medicines</li>
      <li>Blood Pressure and<br>Glucose checks</li>
    </ul>
    <ul>
      <li>Personal care and<br>Beauty Products</li>
      <li>Injectables</li>
      <li>Special Orders</li>
      <li>Delivery service</li>
    </ul>
  </div>

  <div class="footer"></div>

  <div class="hours">
    MONDAY – SATURDAY, THURSDAY 8AM TO 7PM<br>
    SUNDAY 10AM TO 2PM
  </div>

  <div class="c-contact">
    <span><svg class="pin" viewBox="0 0 12 16" aria-hidden="true"><path d="M6 0a6 6 0 0 0-6 6c0 4.5 6 10 6 10s6-5.5 6-10a6 6 0 0 0-6-6zm0 8.5A2.5 2.5 0 1 1 6 3.5a2.5 2.5 0 0 1 0 5z" fill="#3550a3"/></svg>Unit C1, Regent Harbour Hotel, Shore Road, Easthaven</span>
    <span><svg class="phone" viewBox="0 0 16 14" aria-hidden="true"><path d="M2 5c0-3 2-4 6-4s6 1 6 4h-3V3.5H5V5zM3 6h10l1 7H2z" fill="#3550a3"/></svg>555-0155</span>
  </div>

  <div class="social">Visit us on<div class="dot">Linkly</div></div>
</section>

</body>
</html>
```